Dorrow Hollow Ranch all natural beef packaging

I would like a custom label to affix to my packages of steaks, roasts, and burgers. The packaging label should be simple and represent the all natural, healthy and humane way we raise our grass finished and natural grain finished beef. check out www.dorrowhollowranch.example for photos of the ranch and information about our cattle.

Target Market(s)

consumers who wish to purchase beef that is born and raised in Ohio, never given any antibiotics, implants, or hormones. Cattle are never confined, always on pasture, even when finished on grain. Humane treatment of the animals which are handled by horseback and on foot.

Industry/Entity Type

Ranch

Requirements
Must have
• Must be able to incorporate the Prairie Forage Alliance label.
• http://www.prairieforagealliance.example/
• I like dark colors, rich and earthy, but maybe on a white background to stand out on the clear plastic wrap over the beef. Imagine you're buying a steak at Halvins and look at how the packaging stands off from the color of the meat.
Nice to have
• I would like a very simple label that incorporates some icon or picture of a calf or cow. See my website www.dorrowhollowranch.example

```html
<!DOCTYPE html>
<html lang="en">
<head>
<meta charset="utf-8">
<title>Dorrow Hollow Ranch – Beef Label</title>
<link rel="stylesheet" href="https://fonts.googleapis.com/css2?family=Cookie&family=Oswald:wght@600;700&family=Roboto+Condensed:wght@400;700&display=swap">
<style>
  :root {
    --page: #f2f2f2;
    --cream: #f6e6c8;
    --cream-light: #fdf5e6;
    --rim: #7a5a3c;
    --brown: #6a3b1f;
    --brown-soft: #8a5a36;
    --green: #4aa33a;
    --green-dark: #2f7f35;
    --red: #b3182f;
    --pill: #efe6d6;
  }
  html, body {
    margin: 0;
    width: 880px;
    height: 1200px;
    overflow: hidden;
    background: var(--page);
  }
  .canvas {
    width: 880px;
    height: 1200px;
    display: flex;
    align-items: center;
    justify-content: center;
  }
  .label { width: 760px; height: 450px; display: block; }
  .label-body { fill: url(#creamGlow); stroke: var(--rim); stroke-width: 3; }
  .ranch-name { font-family: "Cookie", cursive; font-size: 58px; fill: var(--brown); letter-spacing: 1px; }
  .claims { font-family: "Roboto Condensed", sans-serif; font-size: 12px; font-weight: 700; fill: var(--green); }
  .grass-band { fill: var(--green); }
  .pasture-scene { fill: var(--green); opacity: .85; }
  .alliance-badge { fill: var(--green-dark); stroke: var(--cream-light); stroke-width: 3; }
  .inspection-badge { fill: var(--red); }
  .grassfed { font-family: "Roboto Condensed", sans-serif; font-weight: 700; font-size: 28px; fill: var(--green); letter-spacing: .5px; }
  .product-name { font-family: "Oswald", sans-serif; font-weight: 700; font-size: 62px; fill: var(--brown); }
  .rule { fill: var(--green); }
  .tagline { font-family: "Roboto Condensed", sans-serif; font-size: 14px; fill: var(--green); }
  .origin { font-family: "Roboto Condensed", sans-serif; font-size: 20px; fill: var(--brown); }
  .net-pill { fill: var(--pill); }
  .net-weight { font-family: "Roboto Condensed", sans-serif; font-weight: 700; font-size: 12px; fill: var(--brown); }
  .address { font-family: "Roboto Condensed", sans-serif; font-size: 15px; fill: var(--brown-soft); }
</style>
</head>
<body>
<main class="canvas">
  <svg class="label" viewBox="0 0 760 450" xmlns="http://www.w3.org/2000/svg">
    <defs>
      <radialGradient id="creamGlow" cx="50%" cy="50%" r="60%">
        <stop offset="0%" stop-color="#fdf5e6"/>
        <stop offset="100%" stop-color="#f1dcb6"/>
      </radialGradient>
      <clipPath id="ovalClip"><ellipse cx="380" cy="225" rx="376" ry="221"/></clipPath>
      <path id="titleArc" d="M120 185 Q380 40 640 185"/>
      <path id="addressArc" d="M160 392 Q380 458 600 392"/>
    </defs>

    <ellipse class="label-body" cx="380" cy="225" rx="376" ry="221"/>

    <text class="ranch-name" text-anchor="middle"><textPath href="#titleArc" startOffset="50%">Dorrow Hollow Ranch</textPath></text>

    <g class="claims">
      <text x="340" y="131">✓ NO ANTIBIOTICS.</text>
      <text x="340" y="145">✓ NO ADDED HORMONES.</text>
      <text x="340" y="159">✓ NO GRAINS.</text>
    </g>

    <g clip-path="url(#ovalClip)">
      <rect class="pasture-scene" x="220" y="166" width="270" height="48" rx="6" role="img" aria-label="Green silhouettes of grazing cattle and a rancher on pasture"/>
      <rect class="grass-band" x="0" y="210" width="760" height="16"/>
    </g>

    <circle class="alliance-badge" cx="100" cy="216" r="48" role="img" aria-label="Prairie Forage Alliance certification badge"/>
    <rect class="inspection-badge" x="598" y="176" width="58" height="76" role="img" aria-label="State inspection badge"/>

    <text class="grassfed" x="380" y="260" text-anchor="middle">100% GRASSFED BEEF</text>
    <text class="product-name" x="380" y="322" text-anchor="middle">ANGUS BEEF</text>

    <rect class="rule" x="232" y="329" width="296" height="8"/>
    <text class="tagline" x="380" y="352" text-anchor="middle">AL NATURAL TO OUR CATTLE</text>
    <rect class="rule" x="242" y="357" width="276" height="7"/>
    <text class="origin" x="380" y="386" text-anchor="middle">PRODUCT OF USA</text>

    <rect class="net-pill" x="552" y="264" width="122" height="22" rx="11"/>
    <text class="net-weight" x="564" y="279">NET WT. ______ OZ.</text>

    <text class="address" text-anchor="middle"><textPath href="#addressArc" startOffset="50%">Address: Lorem ipsum dolor sit amet, consectetur adipisci elit.</textPath></text>
  </svg>
</main>
</body>
</html>
```